BOLD & MINIMALIST DESIGN NEEDED

We want a very bold but minimalistic business card design that is impactful and utilizes both sides of the business card. Our current logo is included for your use.

We want bold fonts and good use of negative space. We don't want the logo to overpower the design.

Target Market(s)

Professionals who are building new commercial buildings.

Industry/Entity Type

Construction

Contact Information for Business Card

Name, Title, email, office phone, cell phone, website

Font styles to use
Serif
Sans Serif

Requirements
Must have
• Bold design!

```html
<!DOCTYPE html>
<html lang="en">
<head>
<meta charset="utf-8">
<title>Ridgeline business card</title>
<link rel="stylesheet" href="https://fonts.googleapis.com/css2?family=Poppins:wght@400;500;600;800&display=swap">
<style>
  :root {
    --green: #8cc63f;
    --ink: #0b0c0e;
    --paper: #ffffff;
    --backdrop: #f0f0f0;
    --shadow: rgba(0,0,0,0.28);
  }
  * { margin: 0; padding: 0; box-sizing: border-box; }
  html, body { width: 1200px; height: 987px; overflow: hidden; }
  body {
    background: var(--backdrop);
    font-family: "Poppins", sans-serif;
    color: var(--ink);
    position: relative;
  }
  .card {
    position: absolute;
    left: 247px;
    width: 707px;
    height: 405px;
    background: var(--paper);
    border-radius: 30px;
    border-left: 5px solid var(--green);
    border-bottom: 5px solid var(--green);
    box-shadow: 0 14px 26px var(--shadow);
    overflow: hidden;
  }
  .card--front { top: 67px; }
  .card--back { top: 514px; }

  .wordmark {
    position: absolute;
    font-weight: 800;
    color: var(--ink);
    letter-spacing: 1px;
    line-height: 1;
    white-space: nowrap;
    transform: translate(-50%, -50%);
  }
  .card--front .wordmark { left: 353px; top: 200px; font-size: 72px; }
  .card--back .wordmark { left: 158px; top: 220px; font-size: 44px; }

  .divider {
    position: absolute;
    left: 352px;
    top: 77px;
    width: 1.5px;
    height: 241px;
    background: var(--green);
  }

  .person { position: absolute; left: 409px; top: 96px; }
  .person__name { font-size: 36px; line-height: 1.1; font-weight: 400; letter-spacing: 0.5px; }
  .person__first { color: var(--green); font-weight: 600; }
  .person__title { font-size: 18px; font-weight: 500; margin-top: 4px; }

  .contacts { position: absolute; left: 409px; top: 190px; list-style: none; }
  .contacts li {
    display: flex; align-items: center;
    height: 24.5px;
    font-size: 18px;
    letter-spacing: 0.5px;
  }
  .contacts svg { width: 15px; height: 15px; margin-right: 12px; flex: none; }

  .address-band {
    position: absolute;
    left: 0; top: 347px;
    width: 582px; height: 31px;
    background: var(--green);
    color: var(--paper);
    font-size: 19px;
    line-height: 31px;
    text-align: center;
    padding-left: 30px;
    letter-spacing: 0.3px;
  }
  .ink-band {
    position: absolute;
    left: 646px; top: 347px;
    width: 61px; height: 28px;
    background: var(--ink);
  }
</style>
</head>
<body>

<section class="card card--front" aria-label="Card front">
  <div class="wordmark">RIDGELINE</div>
</section>

<section class="card card--back" aria-label="Card back">
  <div class="wordmark">RIDGELINE</div>
  <div class="divider"></div>

  <div class="person">
    <div class="person__name"><span class="person__first">Marta</span> Kovic</div>
    <div class="person__title">Founder &amp; CEO</div>
  </div>

  <ul class="contacts">
    <li>
      <svg viewBox="0 0 16 16" aria-hidden="true"><path fill="var(--green)" d="M3.6 1.5l2.3 2.6-1.2 1.6c.9 1.9 2.6 3.7 4.6 4.6l1.6-1.2 2.6 2.3-1.2 2.3C7 13.4 2.6 9 1.3 2.7z"/></svg>
      (555) 014-2758
    </li>
    <li>
      <svg viewBox="0 0 16 16" aria-hidden="true"><rect x="4" y="1" width="8" height="14" rx="1.5" fill="none" stroke="var(--green)" stroke-width="1.4"/><circle cx="8" cy="12.6" r="0.9" fill="var(--green)"/></svg>
      (555) 017-9999
    </li>
    <li>
      <svg viewBox="0 0 16 16" aria-hidden="true"><circle cx="8" cy="8" r="6.5" fill="none" stroke="var(--green)" stroke-width="1.4"/><path d="M1.5 8h13M8 1.5c-3 3.5-3 9.5 0 13M8 1.5c3 3.5 3 9.5 0 13" fill="none" stroke="var(--green)" stroke-width="1.1"/></svg>
      www.yourwebsite.com
    </li>
    <li>
      <svg viewBox="0 0 16 16" aria-hidden="true"><rect x="1.5" y="3.5" width="13" height="10" fill="none" stroke="var(--green)" stroke-width="1.4"/><path d="M1.5 4l6.5 5 6.5-5" fill="none" stroke="var(--green)" stroke-width="1.4"/></svg>
      info@yourwebsite.com
    </li>
  </ul>

  <div class="address-band">1480 Summit Ave. Suite 300 Riverton, TX 75001</div>
  <div class="ink-band"></div>
</section>

</body>
</html>
```